New Business Card Design Project

I need a design for business cards, i am an electrical business called "Corvane Electrical and Communications" i need the cards to be double sided with the company logo on the back (attached) the front needs to say my company name, web site, email address, telephone number, and ABN number and electrical license number. I am open to different arrangements of the information but would like the background to be incorporating something electrical or something that looks smart. open to all additional ideas also.

The company colours are orange and grey see logo attached.

Business Name: Corvane Electrical and Communications
Website: corvaneelectricalandcomms.example.com.au
Email: brent@corvaneelectricalandcomms.example.com.au
Telephone(mobile): 0481209736
ABN: 71208349162
Lic No: 418273D

Target Market(s)

Business entities, Project Managers, Accounts, Clients

Industry/Entity Type

Electrician

Contact Information for Business Card

I need a design for business cards, i am an electrical business called "Corvane Electrical and Communications" i need the cards to be double sided with the company logo on the back (attached) the front needs to say my company name

Font styles to use
Serif
Sans Serif

Colors
f37122
5c5c5c

Requirements
Must have
• Must have the Logo on the back open to different ways of it being on the back but had in mind to keep it central but again open to other options
Nice to have
• A real modern cool background that is eye catching yet contemporary
Should not have
• No backgrounds of a light bulb or plug or anything like that

```html
<!DOCTYPE html>
<html lang="en">
<head>
<meta charset="utf-8">
<title>Corvane Electrical and Communications – Business Cards</title>
<link rel="stylesheet" href="https://fonts.googleapis.com/css2?family=PT+Sans:wght@400;700&display=swap">
<style>
  :root {
    --backdrop: #e9e7e4;
    --card-light: #f7f6f4;
    --orange: #fbad18;
    --ink: #231f20;
    --grey: #5c5c5c;
    --black: #000000;
    --faint: #cfcac4;
  }
  * { box-sizing: border-box; margin: 0; padding: 0; }
  html, body {
    width: 1200px; height: 900px; overflow: hidden;
    background: var(--backdrop);
    font-family: "PT Sans", Arial, sans-serif;
    color: var(--ink);
  }
  .canvas { position: relative; width: 1200px; height: 900px; }

  .card {
    position: absolute;
    overflow: hidden;
    box-shadow: 0 6px 18px rgba(0,0,0,0.12);
  }
  .card--front { left: 238px; top: 62px; width: 555px; height: 343px; }
  .card--back  { left: 457px; top: 518px; width: 560px; height: 342px; }

  .card__top {
    position: absolute; left: 0; top: 0; right: 0;
    background: var(--card-light);
    display: flex; flex-direction: column; align-items: center; justify-content: center;
  }
  .card--front .card__top { height: 185px; padding-top: 30px; }
  .card--back .card__top { height: 187px; padding-top: 30px; }

  .brand-name {
    font-weight: 700;
    color: var(--ink);
    text-align: center;
    line-height: 1;
  }
  .brand-name__main { display: block; font-size: 54px; letter-spacing: 4px; }
  .brand-name__sub { display: block; font-size: 12.5px; letter-spacing: 1.6px; margin-top: 8px; }
  .brand-name--faint { color: var(--faint); }

  .contact-band {
    position: absolute; left: 0; right: 0; top: 185px; bottom: 0;
    background: var(--orange);
    display: flex; padding: 36px 0 0 0;
  }
  .person {
    width: 200px; text-align: right; padding-right: 0;
    font-size: 15px; line-height: 1.35;
  }
  .person__name { font-weight: 700; font-size: 18px; }
  .person__role { margin-bottom: 10px; }
  .person__meta { font-weight: 700; }
  .person__meta span { font-weight: 400; }

  .contact-list {
    list-style: none; margin-left: 22px; padding-top: 19px;
    font-size: 13px; line-height: 20px;
  }
  .contact-list li { display: flex; align-items: center; gap: 8px; }
  .contact-list svg { width: 11px; height: 11px; flex: none; fill: var(--ink); }

  .back-band {
    position: absolute; left: 0; right: 0; top: 187px; bottom: 0;
    background: var(--black);
    display: flex; align-items: center; justify-content: center;
  }
  .back-band .brand-name { color: var(--orange); }
  .back-band .brand-name__main { font-size: 46px; }
</style>
</head>
<body>
<main class="canvas">

  <section class="card card--front" aria-label="Business card front">
    <div class="card__top">
      <p class="brand-name">
        <span class="brand-name__main">CORVANE</span>
        <span class="brand-name__sub">ELECTRICAL &amp; COMMUNICATIONS</span>
      </p>
    </div>
    <div class="contact-band">
      <div class="person">
        <p class="person__name">Dale Marsh</p>
        <p class="person__role">Director</p>
        <p class="person__meta">ABN: <span>71208349162</span></p>
        <p class="person__meta">Lic No: <span>418273D</span></p>
      </div>
      <ul class="contact-list">
        <li>
          <svg viewBox="0 0 24 24" aria-hidden="true"><path d="M6.6 10.8a15 15 0 0 0 6.6 6.6l2.2-2.2a1 1 0 0 1 1-.25 11.4 11.4 0 0 0 3.6.57 1 1 0 0 1 1 1V20a1 1 0 0 1-1 1A17 17 0 0 1 3 4a1 1 0 0 1 1-1h3.5a1 1 0 0 1 1 1c0 1.25.2 2.45.57 3.57a1 1 0 0 1-.25 1z"/></svg>
          0481209736
        </li>
        <li>
          <svg viewBox="0 0 24 24" aria-hidden="true"><path d="M2 5h20v14H2z M2 5l10 8 10-8" fill="var(--ink)"/><path d="M3 6l9 7 9-7" stroke="var(--orange)" stroke-width="2" fill="none"/></svg>
          brent@corvaneelectricalandcomms.example.com.au
        </li>
        <li>
          <svg viewBox="0 0 24 24" aria-hidden="true"><circle cx="12" cy="12" r="10"/><path d="M2 12h20M12 2c3 3 3 17 0 20M12 2c-3 3-3 17 0 20" stroke="var(--orange)" stroke-width="1.5" fill="none"/></svg>
          corvaneelectricalandcomms.example.com.au
        </li>
      </ul>
    </div>
  </section>

  <section class="card card--back" aria-label="Business card back">
    <div class="card__top">
      <p class="brand-name brand-name--faint">
        <span class="brand-name__main">CORVANE</span>
        <span class="brand-name__sub">ELECTRICAL &amp; COMMUNICATIONS</span>
      </p>
    </div>
    <div class="back-band">
      <p class="brand-name">
        <span class="brand-name__main">CORVANE</span>
      </p>
    </div>
  </section>

</main>
</body>
</html>
```